Mosquito and outdoor pest management

The uploaded logo must be integrated as the main theme of the card. I would like it to be modern and eye catching. Maybe some backround images or light silver metallic background.
Space enough at the base for contact info to be put in- phone numbers,emails,names,website.
Space on the back for short blog and lines for hand writing..calling card.
Commercial- golf courses, schools, outdoor function properties, pre event treatments.
Residential- retirement villages, townhome complexes and general houses
Management

```html
<!DOCTYPE html>
<html lang="en">
<head>
<meta charset="utf-8">
<title>Bayguard Pest Control – Business Card</title>
<link rel="stylesheet" href="https://fonts.googleapis.com/css2?family=Open+Sans:wght@400;600&display=swap">
<style>
  :root {
    --backdrop: #4a4340;
    --card: #121212;
    --card-edge: #1c1c1c;
    --ink: #f2f2f2;
    --accent: #e3262c;
    --rule: #8a8a8a;
  }
  * { box-sizing: border-box; margin: 0; padding: 0; }
  html, body {
    width: 1200px; height: 814px; overflow: hidden;
    background: var(--backdrop);
    font-family: "Open Sans", Arial, sans-serif;
  }
  .sheet { position: relative; width: 1200px; height: 814px; }
  .card {
    position: absolute; width: 520px; height: 297px;
    background: var(--card);
    border: 1px solid var(--card-edge);
    box-shadow: 0 10px 30px rgba(0,0,0,.35);
  }
  .card--front { left: 55px; top: 259px; }
  .card--back  { left: 625px; top: 259px; }

  .brand { display: flex; align-items: center; gap: 10px; color: var(--ink); }
  .brand__dot { width: 12px; height: 12px; border-radius: 50%; background: var(--accent); flex: none; }
  .brand__name { font-weight: 600; font-size: 28px; letter-spacing: .4px; white-space: nowrap; line-height: 1; }

  .card--front .brand { position: absolute; left: 96px; top: 86px; }

  .person { position: absolute; left: 40px; top: 190px; width: 180px; text-align: right; }
  .person__name { color: var(--accent); font-weight: 600; font-size: 18px; line-height: 1.2; }
  .person__role { color: var(--ink); font-size: 13.5px; margin-top: 4px; }

  .divider { position: absolute; left: 240px; top: 160px; width: 1px; height: 100px; background: var(--rule); }

  .contacts { position: absolute; left: 258px; top: 164px; list-style: none; }
  .contacts li { display: flex; align-items: center; gap: 9px; color: var(--ink); font-size: 13.5px; line-height: 24px; white-space: nowrap; }
  .contacts svg { width: 12px; height: 12px; fill: var(--accent); flex: none; }

  .card--back .brand { position: absolute; left: 0; right: 0; top: 96px; justify-content: center; }
  .site { position: absolute; left: 0; right: 0; top: 220px; text-align: center; color: var(--ink); font-size: 12px; letter-spacing: 5px; }
</style>
</head>
<body>
<main class="sheet">
  <section class="card card--front">
    <div class="brand"><span class="brand__dot"></span><span class="brand__name">Bayguard Pest Control</span></div>
    <div class="person">
      <p class="person__name">Alex Moreton</p>
      <p class="person__role">CEO/Founder</p>
    </div>
    <div class="divider"></div>
    <ul class="contacts">
      <li><svg viewBox="0 0 24 24"><path d="M6.6 10.8a15.1 15.1 0 0 0 6.6 6.6l2.2-2.2c.3-.3.7-.4 1-.2 1.1.4 2.3.6 3.6.6.6 0 1 .4 1 1V20c0 .6-.4 1-1 1A17 17 0 0 1 3 4c0-.6.4-1 1-1h3.5c.6 0 1 .4 1 1 0 1.3.2 2.5.6 3.6.1.3 0 .7-.2 1z"/></svg>555 201 7788</li>
      <li><svg viewBox="0 0 24 24"><path d="M2 5h20v14H2zm2 2v.5l8 5 8-5V7z"/></svg>hello@bayguardpest.com</li>
      <li><svg viewBox="0 0 24 24"><path d="M12 2a10 10 0 1 0 0 20 10 10 0 0 0 0-20zm0 2c1 1.3 1.8 3 2.1 5H9.9C10.2 7 11 5.3 12 4zM4.3 13a8 8 0 0 1 0-2h3.6a17 17 0 0 0 0 2zm.8 2h3.1c.3 1.4.8 2.6 1.4 3.6A8 8 0 0 1 5.1 15zM9.9 13a15 15 0 0 1 0-2h4.2a15 15 0 0 1 0 2zm6.2 0a17 17 0 0 0 0-2h3.6a8 8 0 0 1 0 2zM12 20c-1-1.3-1.8-3-2.1-5h4.2c-.3 2-1.1 3.7-2.1 5zm2.4-1.4c.6-1 1.1-2.2 1.4-3.6h3.1a8 8 0 0 1-4.5 3.6zM15.8 9c-.3-1.4-.8-2.6-1.4-3.6A8 8 0 0 1 18.9 9zM8.2 9H5.1a8 8 0 0 1 4.5-3.6C9 6.4 8.5 7.6 8.2 9z"/></svg>www.bayguardpest.com</li>
    </ul>
  </section>

  <section class="card card--back">
    <div class="brand"><span class="brand__dot"></span><span class="brand__name">Bayguard Pest Control</span></div>
    <p class="site">www.bayguardpest.com</p>
  </section>
</main>
</body>
</html>
```